Car Club Website- RT Marlin Club of New Zealand

We have been running a website in NZ for RT Marlin Car enthusiasts. The design was fairly basic and is in serious need of a revamp, http://kelpwagon.example-host.org/index.html. We are looking for a dynamic design that will be visually attractive ( and obvious ) to our visitors and incorporates the fundamentals of the previous website. The inmportant tabs are the forum, gallery and events and the website needs to be easy to use for everyone.

This is all about the cars and the people. Visually, you need to recognise that we are a NZ Car Club and as such we do not want graphics of Left Hand Drive Cars or anything obviously NOT from NZ.
Thanks, cheers Merv

I AM VERY INTERESTED TO SEE SOMETHING THAT IS TOTALLY DIFFERENT TO ANYTHING YET POSTED. THE DESIGNS WE HAVE ARE GOOD AND I WILL PICK ONE OF THOSE BUT REALLY WANT TO SEE SOMETHING CREATIVE AND EYE CATCHING. I HAVE NOW CHANGED TO NON REFUNDABLE SO SOMEONE WILL GET PAID.
Updates

HI All, thanks for input so far but I have not seen a really creative left field approach yet which I am looking for. Thanks, cheers Merv

Target Market(s)

Car Enthusiasts

Industry/Entity Type

Events

Requirements
Must have
• as per link website
Should not have
• Any obvious graphics not from NZ

```html
<!DOCTYPE html>
<html lang="en">
<head>
<meta charset="utf-8">
<title>Marlin Club of New Zealand</title>
<link href="https://fonts.googleapis.com/css2?family=Questrial&family=PT+Sans:wght@400;700&display=swap" rel="stylesheet">
<style>
:root{
  --ink:#2b2b2b;
  --band:#353535;
  --panel:#333333;
  --panel-dark:#1c1c1c;
  --black:#000000;
  --white:#ffffff;
  --rule:#222222;
  --muted:#bdbdbd;
  --banner:#c9c9c9;
  --footer:#3a3a3a;
}
*{margin:0;padding:0;box-sizing:border-box}
html,body{width:993px;height:1200px;overflow:hidden;background:var(--white)}
.page{position:relative;width:993px;height:1200px;overflow:hidden;font-family:"PT Sans",sans-serif;color:var(--ink)}
.heading-font{font-family:"Questrial",sans-serif}
.abs{position:absolute}

/* header */
.brand{left:102px;top:22px;font-family:"Questrial",sans-serif;color:#3a3a3a;line-height:1}
.brand .name{font-size:44px;display:block}
.brand .sub{font-size:32px;display:block;margin-top:2px}
.social{top:21px;left:770px;display:flex;gap:13px}
.social span{width:27px;height:27px;border-radius:50%;background:#bcbcbc;display:block}
.top-nav{top:102px;right:118px;display:flex;gap:17px;font-family:"Questrial",sans-serif;font-size:12px;color:#222}

/* hero */
.hero{left:0;top:123px;width:993px;height:263px;background:var(--band)}
.hero-photo{position:absolute;left:102px;top:0;width:512px;height:263px;background:linear-gradient(180deg,#c9b9a8 0%,#a59a8e 35%,#2f4f86 55%,#5b5552 80%,#7b726a 100%)}
.hero-copy{position:absolute;left:626px;top:62px;color:var(--white)}
.hero-copy h1{font-family:"Questrial",sans-serif;font-weight:400;font-size:22px}
.hero-copy p{font-size:13px;line-height:15px;margin:16px 0 0 5px;width:250px}
.btn{position:absolute;display:flex;height:30px;font-weight:700;font-size:13px}
.btn .label{background:var(--white);color:#333;display:flex;align-items:center;justify-content:center}
.btn .arrow{background:var(--panel);color:var(--white);display:flex;align-items:center;justify-content:center;font-size:16px}
.hero .btn{left:634px;top:182px}
.hero .btn .label{width:97px}
.hero .btn .arrow{width:38px;background:#1f1f1f}

.dots{top:394px;left:458px;display:flex;gap:7px}
.dots span{width:10px;height:10px;border-radius:50%;background:#333}
.dots span.on{background:var(--white);border:1.5px solid #333}

/* sidebar */
.sidebar{left:102px;top:426px;width:182px;height:360px;background:var(--panel-dark);box-shadow:1px 2px 3px rgba(0,0,0,.4)}
.side-menu{height:171px;background:var(--panel);padding-top:14px}
.side-menu a{display:flex;align-items:center;height:29.5px;color:var(--white);text-decoration:none;font-family:"Questrial",sans-serif;font-size:17px}
.side-menu a::before{content:"";width:25px;height:1px;background:var(--white);margin-right:12px}
.cal-title{display:flex;align-items:center;color:var(--white);font-family:"Questrial",sans-serif;font-size:25px;margin-top:10px}
.cal-title::before{content:"";width:20px;height:2px;background:var(--white);margin-right:8px}
.cal-list{list-style:none;color:var(--white);font-size:11px;margin-top:9px}
.cal-list li{height:26px;display:flex;padding-left:4px}
.cal-list b{font-weight:400;width:40px}
.sidebar .btn{left:0;bottom:0;height:29px}
.sidebar .btn .label{width:145px}
.sidebar .btn .arrow{width:37px}

/* welcome */
.welcome{left:300px;top:422px;width:581px}
.welcome h2{font-family:"Questrial",sans-serif;font-weight:400;font-size:22px;display:flex;align-items:center;color:#222}
.welcome h2::after{content:"";flex:1;height:1px;background:var(--rule);margin-left:8px;margin-top:4px}
.welcome .copy{font-size:10.6px;line-height:12.4px;color:#333;margin-top:8px;padding-left:2px}
.welcome .copy p + p.gap{margin-top:6px}
.welcome-rule{left:300px;top:674px;width:435px;height:1px;background:var(--rule)}
.welcome-btn{left:743px;top:658px}
.welcome-btn .label{width:97px;background:var(--panel);color:var(--white)}
.welcome-btn .arrow{width:37px;background:#111}

/* advertising */
.ads-title{left:303px;top:683px;font-family:"Questrial",sans-serif;font-size:21px;line-height:22px;color:#222}
.ads-title span{display:block;padding-left:14px}
.ads-note{left:304px;top:739px;width:112px;font-family:"Questrial",sans-serif;font-size:7.6px;line-height:9.6px;color:#333}
.ad-banner{left:425px;top:718px;width:454px;height:52px;background:var(--banner);display:flex;align-items:center;justify-content:center;font-size:40px;color:#3a1f1f;letter-spacing:-1px}

/* cards */
.card{top:807px;width:248px;height:308px;background:var(--black);box-shadow:1px 2px 3px rgba(0,0,0,.35)}
.card .photo{height:149px}
.card h3{font-family:"Questrial",sans-serif;font-weight:400;font-size:17px;color:var(--white);margin:11px 0 0 20px}
.card p{font-size:11px;line-height:12.4px;color:var(--white);margin:10px 12px 0 19px}
.card .btn{left:0;bottom:0;height:29px}
.card .btn .label{width:211px;background:var(--white);justify-content:flex-end;padding-right:45px}
.card .btn .arrow{width:37px}
.c1{left:102px}.c2{left:367px}.c3{left:631px}
.c1 .photo{background:linear-gradient(180deg,#8c8a72 0%,#6e6f5d 40%,#2a2f33 65%,#9a9890 100%)}
.c2 .photo{background:linear-gradient(180deg,#9b9488 0%,#2a2f8c 45%,#1a1f6a 75%,#3b3b45 100%)}
.c3 .photo{background:linear-gradient(180deg,#6f7a70 0%,#9db4cc 40%,#b8423f 70%,#d12a2a 100%)}

/* footer */
.footer{left:0;top:1151px;width:993px;height:49px;background:var(--footer);display:flex;justify-content:center;align-items:center;gap:20px;font-family:"Questrial",sans-serif;font-size:12px;color:var(--white);padding-left:0}
</style>
</head>
<body>
<div class="page">

  <header>
    <div class="abs brand"><span class="name">Marlin Club</span><span class="sub">of new Zealand</span></div>
    <div class="abs social" aria-label="Social links"><span></span><span></span><span></span></div>
    <nav class="abs top-nav"><span>FORUM</span><span>GALLERY</span><span>EVENTS</span></nav>
  </header>

  <section class="abs hero">
    <div class="hero-photo" role="img" aria-label="Blue roadster with white stripes parked in a dry hill landscape"></div>
    <div class="hero-copy">
      <h1>Marlin Club</h1>
      <p>Welcome to Marlin Club of New Zealand. We love Marlin’s style At home On the Track or On Show. Share your interest about Marlin's now and join our Club</p>
    </div>
    <div class="btn"><span class="label">Learn More</span><span class="arrow">&gt;</span></div>
  </section>

  <div class="abs dots"><span class="on"></span><span></span><span></span><span></span></div>

  <aside class="abs sidebar">
    <nav class="side-menu">
      <a>Home</a><a>Calendar</a><a>Membership</a><a>Advertisers</a><a>Contact Us</a>
    </nav>
    <div class="cal-title">CALENDAR</div>
    <ul class="cal-list">
      <li><b>15/12</b>Lorem Ipsum is simply...</li>
      <li><b>17/12</b>&nbsp;dummy text...</li>
      <li><b>19/12</b>Lorem Ipsum is simply...</li>
      <li><b>25/12</b>&nbsp;dummy text...</li>
    </ul>
    <div class="btn"><span class="label">Learn More</span><span class="arrow">&gt;</span></div>
  </aside>

  <section class="abs welcome">
    <h2>Welcome to Marlin Club</h2>
    <div class="copy">
      <p>This is not an official website related to the manufacture of RT Marlin cars but it is a website devoted to all those that share a passion for the RT Marlin.<br>
      Welcome to our website. Our aim is to make this site user friendly and we have included a 'Forum' for the benefit of all RT Marlin owners in New Zealand regardless of Marlin kit type. Our intent for the Forum is to give those people interested/active in the RT Marlin NZ scene a common vehicle to share ideas, problem solve and plan events.<br>
      Our Calendar lists up-to-date and upcoming events. Check this regularly, especially for those last-minute runs that are often organised at very short notice upon the discovery of fine weather in Auckland!</p>
      <p class="gap">No matter where your taste lies, the Marlin Club of New Zealand has members that fit all categories.<br>
      From showing your prize possession off at a local car show or promotional event, to risking it all on the race track. If you’re into Marlin’s then this is the place to be!<br>
      The club regularly attends shows such as the Concours of Style at Kauri Park, All Classics Day and fundraising events such as the Men's Health Runs.&nbsp; Just for that adrenalin rush a few hot laps at Ridgeway Park or even Coast Rally, to test your nerves!<br>
      So if you’re into Marlin’s, thinking of building one, looking for advice, or just need to be near one check out the Calendar pages or contact details</p>
    </div>
  </section>
  <div class="abs welcome-rule"></div>
  <div class="btn welcome-btn"><span class="label">Learn More</span><span class="arrow">&gt;</span></div>

  <div class="abs ads-title">Advertising<span>Banners</span></div>
  <p class="abs ads-note">PLEASE SUPPORT OUR ADVERTISERS WHO FUND THIS SITE FOR THE BENEFIT OF ALL</p>
  <div class="abs ad-banner">southgatemotors</div>

  <article class="abs card c1">
    <div class="photo" role="img" aria-label="Dark roadster parked in front of a house"></div>
    <h3>Fest no1</h3>
    <p>Lorem Ipsum is simply dummy text of the printing and typesetting industry. Lorem Ipsum has been the industry's standard dummy text ever since the 1500s, when an unknown printer took a galley of type and scrambled.</p>
    <div class="btn"><span class="label">Learn More</span><span class="arrow">&gt;</span></div>
  </article>
  <article class="abs card c2">
    <div class="photo" role="img" aria-label="Deep blue roadster at a car show"></div>
    <h3>Fest no1</h3>
    <p>Lorem Ipsum is simply dummy text of the printing and typesetting industry. Lorem Ipsum has been the industry's standard dummy text ever since the 1500s, when an unknown printer took a galley of type and scrambled.</p>
    <div class="btn"><span class="label">Learn More</span><span class="arrow">&gt;</span></div>
  </article>
  <article class="abs card c3">
    <div class="photo" role="img" aria-label="Row of silver and red roadsters lined up outdoors"></div>
    <h3>Fest no3</h3>
    <p>Lorem Ipsum is simply dummy text of the printing and typesetting industry. Lorem Ipsum has been the industry's standard dummy text ever since the 1500s, when an unknown printer took a galley of type and scrambled.</p>
    <div class="btn"><span class="label">Learn More</span><span class="arrow">&gt;</span></div>
  </article>

  <footer class="abs footer">
    <span>HOME</span><span>CALENDAR</span><span>MEMBERSHIP</span><span>ADVERTISERS</span><span>CONTACT US</span><span>FORUM</span><span>GALLERY</span><span>EVENTS</span>
  </footer>

</div>
</body>
</html>
```